Velmarotix - world unique technology for better life - please let them know who am i at first sight

We need a new business card for company which is a provider of unique crystal based technology suitable for all living being. For more information and final design you can use our brochure (our colours are black and blue from brochure).
We use Verdana font

Industry/Entity Type

Business

Contact Information for Business Card

regular dimension

Font styles to use
Other font styles liked:
• Verdana

Requirements
Must have
• Logo
• name
• function/position
• phone
• mobile
• e-mail
• adress
Nice to have
• inovative design (technology directed)

```html
<!DOCTYPE html>
<html lang="en">
<head>
<meta charset="utf-8">
<title>Velmarotix business card</title>
<link rel="stylesheet" href="https://fonts.googleapis.com/css2?family=Noto+Sans:wght@300;700&display=swap">
<style>
  :root {
    --stage: #8c8c8c;
    --paper: #f4f4f2;
    --brand-blue: #0f9ad6;
    --brand-blue-light: #2fb0e6;
    --brand-blue-deep: #0a86c4;
    --pattern-tone: #8fd0ef;
    --text-light: #ffffff;
  }
  * { box-sizing: border-box; margin: 0; padding: 0; }
  html, body {
    width: 1200px; height: 1000px; overflow: hidden;
    background: var(--stage);
    font-family: "Noto Sans", Verdana, sans-serif;
  }
  .canvas { position: relative; width: 1200px; height: 1000px; }

  .card {
    position: absolute;
    background: var(--paper);
    box-shadow: 0 6px 18px rgba(0,0,0,.25);
    overflow: hidden;
  }

  /* Logo side */
  .card-back { left: 580px; top: 70px; width: 560px; height: 320px; }
  .card-back .brand {
    position: absolute; left: 70px; top: 124px;
    display: flex; align-items: center; gap: 22px;
  }
  .brand-dot { border-radius: 50%; background: var(--brand-blue); flex: none; }
  .card-back .brand-dot { width: 72px; height: 72px; }
  .brand-name {
    font-weight: 300; color: var(--brand-blue);
    letter-spacing: 2px; text-transform: uppercase; white-space: nowrap;
  }
  .card-back .brand-name { font-size: 44px; }

  /* Contact side */
  .card-front { left: 60px; top: 480px; width: 680px; height: 390px; }
  .card-front .shapes { position: absolute; inset: 0; }
  .card-front .brand {
    position: absolute; left: 36px; top: 150px;
    display: flex; align-items: center; gap: 14px;
  }
  .card-front .brand-dot { width: 44px; height: 44px; }
  .card-front .brand-name { font-size: 28px; }

  .name-tag {
    position: absolute; left: 390px; top: 112px; width: 220px;
    text-align: center; color: var(--brand-blue-deep); font-weight: 700;
  }
  .person-name { font-size: 24px; line-height: 1.15; }
  .person-role { font-size: 18px; line-height: 1.2; }

  .contact-list {
    position: absolute; left: 364px; top: 236px;
    list-style: none; color: var(--text-light); font-weight: 700;
    font-size: 16px; line-height: 1.55; white-space: nowrap;
  }
  .contact-list .address { margin-top: 6px; }
</style>
</head>
<body>
<main class="canvas">

  <section class="card card-back" aria-label="Card back with company name">
    <div class="brand">
      <span class="brand-dot"></span>
      <span class="brand-name">Velmarotix</span>
    </div>
  </section>

  <section class="card card-front" aria-label="Card front with contact details">
    <svg class="shapes" width="680" height="390" viewBox="0 0 680 390">
      <defs>
        <linearGradient id="blue-field" x1="0" y1="0" x2="1" y2="1">
          <stop offset="0" stop-color="#0f9ad6"/>
          <stop offset="1" stop-color="#2fb0e6"/>
        </linearGradient>
        <radialGradient id="pattern-fill" cx="0.5" cy="0.5" r="0.5">
          <stop offset="0" stop-color="#ffffff"/>
          <stop offset="1" stop-color="#8fd0ef"/>
        </radialGradient>
      </defs>
      <rect class="blue-field" x="0" y="0" width="680" height="390" fill="url(#blue-field)"/>
      <path class="white-field" d="M0 0 H440 C400 160 330 300 250 390 H0 Z" fill="#f4f4f2"/>
      <g role="img" aria-label="Decorative crystal lattice pattern">
        <path d="M170 0 A120 100 0 0 0 410 0 Z" fill="url(#pattern-fill)"/>
      </g>
      <g role="img" aria-label="Decorative crystal lattice pattern">
        <path d="M0 390 L0 300 A150 130 0 0 1 300 390 Z" fill="url(#pattern-fill)"/>
      </g>
      <path class="name-pill" d="M340 106 H600 A34 34 0 0 1 600 174 H340 Z" fill="#f4f4f2"/>
    </svg>

    <div class="brand">
      <span class="brand-dot"></span>
      <span class="brand-name">Velmarotix</span>
    </div>

    <div class="name-tag">
      <p class="person-name">Your Name</p>
      <p class="person-role">Position</p>
    </div>

    <ul class="contact-list">
      <li>Phone : 012- 345- 6789</li>
      <li>Mobile : 098- 765- 4321</li>
      <li>Email : yourname@mail.com</li>
      <li class="address">Address which you want to provide</li>
    </ul>
  </section>

</main>
</body>
</html>
```